PWRPT design for Company

Project: Develop a pwrpt for QT7lx. This can be just a blank pwrpt with standard templates that we can use to build our content and solutions around.
Website: www.qt7lx.example
Color Pallet: Try to use the color schema from our website.
PWRPT Design Tips: While we are a research-based company, our primary target is schools and school districts. We say our work is RESEARCH, POLICY, AND PRACTICE. I would like images that represent “WHY” our research matters, i.e. students, teachers, and administrators. If you can use images and stock photos that represent students with diverse backgrounds, teachers that are diverse and clearly teaching, and administrators that run a school, university, etc. We are in the process of updating our website, but the color scheme will remain the same.
Additional Information:
We built, researched, and designed, www.brvo-kt.example .
We built, researched, and designed, http://67pwgamma.example/olar/index.html
Target Market(s)
EDUCATION
Industry/Entity Type
It Company
Look and feel

```html
<!DOCTYPE html>
<html lang="en">
<head>
<meta charset="utf-8">
<title>QT7lx – Welcome Slide</title>
<link rel="stylesheet" href="https://fonts.googleapis.com/css2?family=Montserrat:wght@800&family=Lato:ital,wght@0,300;0,400;1,300&display=swap">
<style>
  :root {
    --orange: #f47e20;
    --photo-dark: #1f2a36;
    --photo-mid: #5b6877;
    --photo-light: #aeb6bf;
    --white: #ffffff;
    --ink: #3c3c3c;
    --logo-grey: #6a6d70;
    --footer-bar: #4d5b5f;
  }
  * { margin: 0; padding: 0; box-sizing: border-box; }
  html, body { width: 1200px; height: 900px; overflow: hidden; background: var(--white); }
  .slide { position: relative; width: 1200px; height: 900px; overflow: hidden; font-family: "Lato", sans-serif; }

  .hero { position: absolute; left: 0; top: 0; width: 1200px; height: 735px; }
  .hero-photo {
    position: absolute; inset: 0;
    background: linear-gradient(100deg, var(--photo-mid) 0%, var(--photo-dark) 30%, var(--photo-mid) 55%, var(--photo-light) 100%);
  }
  .hero-accent { position: absolute; inset: 0; }

  .title-block { position: absolute; left: 600px; top: 392px; color: var(--white); }
  .title-welcome { font-family: "Montserrat", sans-serif; font-weight: 800; font-size: 57px; line-height: 1; letter-spacing: 0.5px; }
  .title-program { font-weight: 300; font-size: 37px; line-height: 1; margin-top: 16px; }
  .title-date { font-weight: 300; font-size: 25px; line-height: 1; margin-top: 32px; }

  .footer { position: absolute; left: 0; top: 735px; width: 1200px; height: 143px; background: var(--white); }
  .legal { position: absolute; left: 38px; top: 52px; width: 790px; font-style: italic; font-weight: 300; font-size: 16px; line-height: 26px; color: var(--ink); }
  .brand { position: absolute; left: 805px; top: 22px; width: 350px; }
  .brand-row { display: flex; align-items: center; gap: 20px; }
  .brand-mark { width: 60px; height: 60px; background: var(--orange); flex: none; }
  .brand-name { font-weight: 400; font-size: 80px; line-height: 1; color: var(--logo-grey); letter-spacing: 1px; }
  .brand-tagline { margin-top: 14px; margin-left: 100px; font-size: 14px; letter-spacing: 1.6px; color: var(--logo-grey); }

  .footer-bar { position: absolute; left: 0; top: 878px; width: 1200px; height: 22px; background: var(--footer-bar); }
</style>
</head>
<body>
<main class="slide">
  <section class="hero">
    <div class="hero-photo" role="img" aria-label="Photo of a businessman in a suit pointing at a rising line chart"></div>
    <svg class="hero-accent" width="1200" height="735" viewBox="0 0 1200 735" aria-hidden="true">
      <defs>
        <linearGradient id="accentFill" x1="0" y1="0" x2="1" y2="1">
          <stop offset="0" stop-color="#f58a2c"/>
          <stop offset="1" stop-color="#ec7418"/>
        </linearGradient>
      </defs>
      <polygon points="692,0 1200,0 1200,735 382,735" fill="url(#accentFill)" opacity="0.93"/>
    </svg>
    <div class="title-block">
      <h1 class="title-welcome">WELCOME</h1>
      <p class="title-program">Route2Futures (R2F)</p>
      <p class="title-date">August 21st, 2017</p>
    </div>
  </section>

  <footer class="footer">
    <p class="legal">© 2017 All rights reserved. Contains confidential and proprietary information and may<br>not be disclosed or reproduced without &nbsp;the prior written consent of QT7lx</p>
    <div class="brand">
      <div class="brand-row">
        <span class="brand-mark"></span>
        <span class="brand-name">QT7lx</span>
      </div>
      <p class="brand-tagline">EVIDENCE + INSIGHT + IMPACT</p>
    </div>
  </footer>
  <div class="footer-bar"></div>
</main>
</body>
</html>
```